Business Card: RW Office Partners - Your organised problem solver

Business Name: RW Office Partners
Website: www.rwofficepartners.com.au
Email: marisol@rwofficepartners.com.au
Mobile: 61 482 907 236
Facebook: @rwofficepartners
Instrgram: @rwofficepartners

Brading Colours:
HEX
#986474
#ddccd3
#7a8498
#c9d8e4
#000000
#ffffff

Tag Line: Your reliable admin partner

Link to DRAFT website:
https://deskhelpcollective.wixsite.com/rw-office-partners

About Page from the website:
My name is Marisol Wrenfield, and I would love to assist you to become more productive in your day to day and achieve your business and personal goals.
My mission is to give you time, time to work on the important tasks of your business or to be able to spend more time with your family. I will take on the tasks you don’t have time for, don’t know well or simply don’t like to do.
I have an extensive background in Administration, Tender Coordination, Document Control, WHS and Quality Management working primarily in the Construction, Mining and Corporate World.
I am passionate about being organised, having order and making things in your life (and mine) easier! I love to watch something unfold and grow into something amazing! I am known for being the go-to problem solver, the organiser of all things, producing high standards of work even under pressure. I’m also a confident communicator, and I understand that you’re busy running your business.

Target Market(s)

Small to Medium Business who require assistance in their business by a virtual assistant.

Industry/Entity Type

Virtual Assistant

Contact Information for Business Card

Mobile: 61 482 907 236

Font styles to use
Sans Serif

Colors
ffffff

Requirements
Must have
• Branding Colours as outlined.
Contact Details as outlined.
Logo as provided.
Proper contact details - mobile, facebook, instragm, website.
Simple, Elegant, very clean looking.
Should not have
• Note cute with pictures.
Not too girly as still want to market to construction companies.

```html
<!DOCTYPE html>
<html lang="en">
<head>
<meta charset="utf-8">
<title>RW Office Partners – Business Card</title>
<link rel="stylesheet" href="https://fonts.googleapis.com/css2?family=Exo+2:wght@600&family=Roboto:wght@400&display=swap">
<style>
  :root {
    --brand-mauve: #986474;
    --ink-mauve: #7b4c5b;
    --blush: #ddccd3;
    --slate: #7a8498;
    --mist: #c9d8e4;
    --paper: #f6f2f3;
    --backdrop: #e7e1e3;
    --white: #ffffff;
    --text-dark: #2b2528;
  }
  html, body {
    margin: 0;
    padding: 0;
    width: 1200px;
    height: 1054px;
    overflow: hidden;
    background: var(--backdrop);
  }
  .business-card {
    position: absolute;
    left: 100px;
    top: 225px;
    width: 1000px;
    height: 603px;
    border-radius: 22px;
    background: var(--paper);
    box-shadow: 0 12px 40px rgba(90, 60, 70, 0.18);
    overflow: hidden;
    font-family: "Roboto", Arial, sans-serif;
  }
  .holder-name {
    position: absolute;
    left: 53px;
    top: 72px;
    margin: 0;
    font-family: "Exo 2", "Trebuchet MS", sans-serif;
    font-weight: 600;
    font-size: 37px;
    line-height: 1.2;
    color: var(--ink-mauve);
    letter-spacing: 0.2px;
  }
  .holder-role {
    position: absolute;
    left: 53px;
    top: 122px;
    margin: 0;
    font-size: 23px;
    line-height: 1.2;
    color: var(--text-dark);
  }
  .brand-mark {
    position: absolute;
    right: 52px;
    top: 92px;
    display: flex;
    align-items: center;
    gap: 22px;
  }
  .brand-mark__square {
    width: 26px;
    height: 26px;
    background: var(--ink-mauve);
  }
  .brand-mark__name {
    font-family: "Exo 2", "Trebuchet MS", sans-serif;
    font-weight: 600;
    font-size: 54px;
    line-height: 1.05;
    color: var(--ink-mauve);
    text-align: right;
  }
  .company-name {
    position: absolute;
    left: 53px;
    top: 318px;
    margin: 0;
    font-family: "Exo 2", "Trebuchet MS", sans-serif;
    font-weight: 600;
    font-size: 31px;
    color: var(--ink-mauve);
  }
  .contact-list {
    position: absolute;
    left: 53px;
    top: 374px;
    margin: 0;
    padding: 0;
    list-style: none;
  }
  .contact-list li {
    display: flex;
    align-items: center;
    height: 38px;
    font-size: 23px;
    color: var(--text-dark);
  }
  .contact-icon {
    width: 22px;
    height: 22px;
    margin-right: 22px;
    flex: none;
    fill: var(--text-dark);
  }
  .social-square {
    width: 18px;
    height: 18px;
    margin: 0 24px 0 2px;
    border-radius: 3px;
    background: var(--text-dark);
    flex: none;
  }
  .tagline-band {
    position: absolute;
    left: 0;
    top: 0;
    width: 1000px;
    height: 603px;
  }
  .tagline {
    position: absolute;
    left: 589px;
    top: 548px;
    margin: 0;
    font-size: 23px;
    color: var(--blush);
    letter-spacing: 0.2px;
  }
</style>
</head>
<body>
  <section class="business-card">
    <svg class="tagline-band" viewBox="0 0 1000 603" aria-hidden="true">
      <polygon points="530,603 566,530 1000,530 1000,603" fill="var(--ink-mauve)"/>
    </svg>

    <h1 class="holder-name">Marisol Wrenfield</h1>
    <p class="holder-role">Virtual Assistant</p>

    <div class="brand-mark">
      <span class="brand-mark__square"></span>
      <span class="brand-mark__name">RW Office<br>Partners</span>
    </div>

    <h2 class="company-name">RW Office Partners</h2>

    <ul class="contact-list">
      <li>
        <svg class="contact-icon" viewBox="0 0 24 24" aria-hidden="true">
          <path d="M3 8c0-3 4-4 9-4s9 1 9 4v2h-5V8H8v2H3z"/>
          <path d="M6 11h12l2 9H4z M12 13a3 3 0 1 0 0 6a3 3 0 1 0 0-6z"/>
        </svg>
        <span>61 482 907 236</span>
      </li>
      <li>
        <svg class="contact-icon" viewBox="0 0 24 24" aria-hidden="true">
          <path d="M2 5h20v14H2z M4 7v1l8 5 8-5V7l-8 5z" fill-rule="evenodd"/>
        </svg>
        <span>marisol@rwofficepartners.com.au</span>
      </li>
      <li>
        <svg class="contact-icon" viewBox="0 0 24 24" aria-hidden="true">
          <g fill="none" stroke="#2b2528" stroke-width="1.8">
            <circle cx="12" cy="12" r="9"/>
            <ellipse cx="12" cy="12" rx="4" ry="9"/>
            <line x1="3" y1="12" x2="21" y2="12"/>
          </g>
        </svg>
        <span>www.rwofficepartners.com.au</span>
      </li>
      <li>
        <span class="social-square"></span>
        <span>@rwofficepartners</span>
      </li>
      <li>
        <span class="social-square"></span>
        <span>@rwofficepartners</span>
      </li>
    </ul>

    <p class="tagline">Your reliable admin partner</p>
  </section>
</body>
</html>
```